Business card for builder specialising in renovations.

Need a card for our building business. Business name is under Martin Powles.
Have licence number on card ( 527691K)
Contact number (0400 382 415)
Want to work on logo for some business cards and shirts - something with MP or MPB or open to ideas??
No animations, No hammers. Something sharp and eye catching.
Highlight that we are a renovation specialist. Simple on front with extra details on back with some lines to jot down things.

Target Market(s)

Renovators

Industry/Entity Type

Building

Contact Information for Business Card

2 sided with room on back to jot things down.
Extra details on back so front can be simple ..like, renovations, bathrooms, decks, extensions, new builds,

Logo Text

MP

Font styles to use
Serif

Requirements
Must have
• Eye catching design .
• Name : Martin powles
• Licence number
• Contact number - 0400382415
Nice to have
• Some logo design that we can carry through to other forms of advertising
• Local builder
• Quality work
Should not have
• No animations

```html
<!DOCTYPE html>
<html lang="en">
<head>
<meta charset="utf-8">
<title>Martin Powles — Business Card</title>
<link href="https://fonts.googleapis.com/css2?family=Tinos:wght@400;700&display=swap" rel="stylesheet">
<style>
  :root {
    --brand-blue: #25a7e0;
    --ink: #111418;
    --paper: #ffffff;
    --backdrop: #2b2b2d;
  }
  * { box-sizing: border-box; margin: 0; padding: 0; }
  html, body { width: 1200px; height: 900px; overflow: hidden; }
  body {
    background: var(--backdrop);
    font-family: "Tinos", "Times New Roman", serif;
    color: var(--ink);
    position: relative;
  }
  .card {
    position: absolute;
    width: 600px;
    height: 343px;
    background: var(--paper);
    overflow: hidden;
    box-shadow: 0 8px 24px rgba(0,0,0,0.45);
  }
  .card--front { left: 100px; top: 80px; }
  .card--back { left: 500px; top: 477px; }

  .brand-mark {
    display: block;
    background: var(--brand-blue);
    border: 2px solid var(--ink);
    box-shadow: 3px 3px 0 rgba(0,0,0,0.25);
  }
  .brand-name {
    font-weight: 700;
    text-transform: uppercase;
    color: var(--ink);
    letter-spacing: 0.5px;
    white-space: nowrap;
  }

  /* Front */
  .front-lockup {
    position: absolute;
    left: 0; right: 0; top: 46px;
    display: flex; flex-direction: column; align-items: center;
  }
  .front-lockup .brand-mark { width: 152px; height: 152px; }
  .front-lockup .brand-name { font-size: 25px; margin-top: 6px; line-height: 1; }
  .front-web {
    font-size: 16px; color: var(--brand-blue); margin-top: 4px; letter-spacing: 0.3px;
  }
  .services {
    position: absolute;
    left: 34px; right: 34px; bottom: 34px;
    border: 2px solid var(--brand-blue);
    padding: 5px 10px;
    display: flex; justify-content: space-between; align-items: center;
    font-size: 16px; text-transform: uppercase; letter-spacing: 0.3px;
  }
  .services .dot {
    width: 8px; height: 8px; background: var(--brand-blue); display: inline-block;
  }

  /* Back */
  .back-logo {
    position: absolute; left: 0; top: 0; width: 290px; height: 100%;
    display: flex; flex-direction: column; align-items: center; justify-content: center;
  }
  .back-logo .brand-mark { width: 176px; height: 176px; }
  .back-logo .brand-name { font-size: 26px; margin-top: 8px; line-height: 1; }
  .back-panel {
    position: absolute; left: 290px; top: 0; right: 0; bottom: 0;
    background: var(--brand-blue);
    color: var(--paper);
    padding: 72px 0 0 40px;
  }
  .back-panel::before {
    content: ""; position: absolute; left: -22px; top: 118px;
    border-style: solid; border-width: 16px 22px 16px 0;
    border-color: transparent var(--brand-blue) transparent transparent;
  }
  .contact-name {
    font-size: 24px; font-weight: 700; color: var(--ink);
    text-transform: uppercase; line-height: 1; margin-bottom: 6px;
  }
  .contact-role, .contact-licence { font-size: 16px; line-height: 1.3; }
  .contact-list { list-style: none; margin-top: 4px; padding-left: 16px; }
  .contact-list li {
    font-size: 16px; line-height: 1.35; display: flex; align-items: center; gap: 8px;
  }
  .contact-list svg { width: 12px; height: 12px; flex: none; }
</style>
</head>
<body>

<section class="card card--front" aria-label="Business card front">
  <div class="front-lockup">
    <span class="brand-mark" aria-hidden="true"></span>
    <span class="brand-name">Martin Powles</span>
    <span class="front-web">www.martinpowles.com</span>
  </div>
  <div class="services">
    <span>Renovations</span><span class="dot"></span>
    <span>Bathrooms Decks</span><span class="dot"></span>
    <span>Extensions</span><span class="dot"></span>
    <span>New Builds</span>
  </div>
</section>

<section class="card card--back" aria-label="Business card back">
  <div class="back-logo">
    <span class="brand-mark" aria-hidden="true"></span>
    <span class="brand-name">Martin Powles</span>
  </div>
  <div class="back-panel">
    <p class="contact-name">Martin Powles</p>
    <p class="contact-role">Director</p>
    <p class="contact-licence">Licence: (527691K)</p>
    <ul class="contact-list">
      <li>
        <svg viewBox="0 0 12 12" aria-hidden="true"><path d="M2.5 1 L4.5 1 L5 3.5 L3.8 4.4 Q5 7 7.6 8.2 L8.5 7 L11 7.5 L11 9.5 Q10.5 11 9 11 Q1 10 1 3 Q1 1.5 2.5 1 Z" fill="#111418"/></svg>
        0400382415
      </li>
      <li>
        <svg viewBox="0 0 12 12" aria-hidden="true"><rect x="1" y="2.5" width="10" height="7" fill="none" stroke="#111418" stroke-width="1.2"/><path d="M1 2.5 L6 6.5 L11 2.5" fill="none" stroke="#111418" stroke-width="1.2"/></svg>
        info@martinpowles.com
      </li>
      <li>
        <svg viewBox="0 0 12 12" aria-hidden="true"><circle cx="6" cy="6" r="5" fill="none" stroke="#111418" stroke-width="1.1"/><ellipse cx="6" cy="6" rx="2.2" ry="5" fill="none" stroke="#111418" stroke-width="1"/><path d="M1 6 H11" stroke="#111418" stroke-width="1"/></svg>
        www.martinpowles.com
      </li>
    </ul>
  </div>
</section>

</body>
</html>
```